Moonridge Real Estate Sign

We are in the process of rebranding our business and need a new For Sale \ Sold sign.
We're a prestige real estate agency and therefore require a really stylish sign.
I've uploaded the following files
1. The new company logo
2. "sample sign.jpg" which shows the type of sign we would like. It is a metal sign with a top panel and bottom panel.
3. Our previous sign "previous sign.jpg" if you're interested in seeing it.
The sign must be black with white text.
Our thoughts are that the top panel (refer to sample sign) would contain the text "For Sale" or "Sold". These would be two separate panels which are interchangeable and could be screwed in place.
The bottom panel would not contain any photos like the sample. However, it may contain our logo and my contact details etc.
The sign is 900mm wide x 1200mm high.
My details are:
Name: Gerald Fenwick
Web: www.mrrealestate.com.au
Email: sales@mrrealestate.com.au
Phone: 0491 806 357

```html
<!DOCTYPE html>
<html lang="en">
<head>
<meta charset="utf-8">
<title>Moonridge Real Estate – For Sale / Sold Signs</title>
<link rel="stylesheet" href="https://fonts.googleapis.com/css2?family=Arimo:wght@700&family=Tinos:wght@700&family=Montserrat:wght@500&display=swap">
<style>
  :root {
    --sign-black: #000000;
    --sign-white: #ffffff;
    --page-bg: #ffffff;
  }
  * { box-sizing: border-box; margin: 0; padding: 0; }
  html, body {
    width: 1200px;
    height: 779px;
    overflow: hidden;
    background: var(--page-bg);
  }
  .canvas {
    position: relative;
    width: 1200px;
    height: 779px;
  }
  .sign {
    position: absolute;
    top: 0;
    width: 584px;
    height: 779px;
    background: var(--sign-black);
    color: var(--sign-white);
  }
  .sign--for-sale { left: 0; }
  .sign--sold { left: 616px; }

  .sign__header {
    position: absolute;
    top: 46px;
    left: 0;
    width: 100%;
    height: 83px;
    background: var(--sign-white);
    color: var(--sign-black);
    display: flex;
    align-items: center;
    justify-content: center;
    font-family: "Arimo", Arial, sans-serif;
    font-weight: 700;
    font-size: 56px;
    letter-spacing: 1px;
    line-height: 1;
  }

  .brand {
    position: absolute;
    top: 244px;
    left: 68px;
    height: 144px;
    display: flex;
    align-items: center;
  }
  .brand__mark {
    width: 86px;
    height: 86px;
    background: var(--sign-white);
  }
  .brand__divider {
    width: 2px;
    height: 144px;
    background: var(--sign-white);
    margin: 0 22px;
  }
  .brand__name {
    font-family: "Montserrat", Arial, sans-serif;
    font-weight: 500;
    color: var(--sign-white);
    line-height: 1;
    text-align: center;
  }
  .brand__name-main {
    display: block;
    font-size: 56px;
    letter-spacing: -1px;
  }
  .brand__name-sub {
    display: block;
    font-size: 23px;
    letter-spacing: 5px;
    margin-top: 6px;
  }

  .contact-line {
    position: absolute;
    top: 394px;
    left: 0;
    width: 100%;
    text-align: center;
    font-family: "Tinos", "Times New Roman", serif;
    font-weight: 700;
    font-size: 15px;
    word-spacing: 1px;
  }
  .contact-line__item + .contact-line__item { margin-left: 14px; }

  .agent {
    position: absolute;
    top: 604px;
    left: 0;
    width: 100%;
    text-align: center;
    font-family: "Tinos", "Times New Roman", serif;
    font-weight: 700;
    line-height: 1;
  }
  .agent__name { font-size: 52px; }
  .agent__phone {
    font-size: 74px;
    margin-top: 10px;
  }
</style>
</head>
<body>
<main class="canvas">

  <section class="sign sign--for-sale">
    <h1 class="sign__header">FOR SALE</h1>
    <div class="brand">
      <div class="brand__mark"></div>
      <div class="brand__divider"></div>
      <p class="brand__name">
        <span class="brand__name-main">Moonridge</span>
        <span class="brand__name-sub">REAL ESTATE</span>
      </p>
    </div>
    <p class="contact-line">
      <span class="contact-line__item">Web: www.mrrealestate.com.au</span>
      <span class="contact-line__item">Email: sales@mrrealestate.com.au</span>
    </p>
    <div class="agent">
      <p class="agent__name">Gerald Fenwick</p>
      <p class="agent__phone">0491 806 357</p>
    </div>
  </section>

  <section class="sign sign--sold">
    <h1 class="sign__header">SOLD</h1>
    <div class="brand">
      <div class="brand__mark"></div>
      <div class="brand__divider"></div>
      <p class="brand__name">
        <span class="brand__name-main">Moonridge</span>
        <span class="brand__name-sub">REAL ESTATE</span>
      </p>
    </div>
    <p class="contact-line">
      <span class="contact-line__item">Web: www.mrrealestate.com.au</span>
      <span class="contact-line__item">Email: sales@mrrealestate.com.au</span>
    </p>
    <div class="agent">
      <p class="agent__name">Gerald Fenwick</p>
      <p class="agent__phone">0491 806 357</p>
    </div>
  </section>

</main>
</body>
</html>
```